GTP biz card

We need a business card design for our new company based in Los Angeles called "Gold Tide Pictures". We develop film and television projects. We work with investors, financiers, film production companies, film distribution and sales companies as well as studios. We would like to incorporate our logo (see attached) on a two-sided card. We need to include: name and title, address, phone, email and company website.

Target Market(s)

Business, financial and studio clients

Industry/Entity Type

Business

Contact Information for Business Card

Two-sided. We are thinking of the logo on one side and the information on the back. Please feel free to be creative! Thanks.

Requirements
Must have
• Please include the following text information, excluding the "CAPS CATEGORY:" and please allow the ability for us to change the name, title and email address for each company employee):
• NAME & TITLE:
• Neil Parker
• Managing Partner
• COMPANY NAME:
• GOLD TIDE PICTURES (please use existing logo)
• COMPANY ADDRESS:
• KTW Studio Park
• 2250 Halverd Street
• Harbor Wing, 4th Floor
• Manhattan Beach, CA 90412
• COMPANY PHONE NUMBER:
• 310-555-0148
• COMPANY WEBSITE ADDRESS:
• www.goldtidepicturesgroup.example
• EMAIL ADDRESS: (only one per card)
• peter@goldtidepicturesgroup.example
• bingo@goldtidepicturesgroup.example
• neil@goldtidepicturesgroup.example

```html
<!DOCTYPE html>
<html lang="en">
<head>
<meta charset="utf-8">
<title>Gold Tide Pictures – Business Card</title>
<link rel="stylesheet" href="https://fonts.googleapis.com/css2?family=Josefin+Sans:wght@400;600&family=Montserrat:wght@600;700&display=swap">
<style>
  :root {
    --backdrop: #ececec;
    --card-black: #030405;
    --card-white: #ffffff;
    --accent-blue: #1ba7e2;
    --ink: #111111;
    --muted-white: #e9eef2;
  }
  * { box-sizing: border-box; margin: 0; padding: 0; }
  html, body {
    width: 1023px; height: 1200px; overflow: hidden;
    background: var(--backdrop);
  }
  .stage { position: relative; width: 1023px; height: 1200px; }

  .card {
    position: absolute; left: 188px; width: 652px; height: 381px;
    box-shadow: 0 2px 6px rgba(0,0,0,0.25);
    overflow: hidden;
  }
  .card--front { top: 167px; background: var(--card-black); }
  .card--back { top: 638px; background: var(--card-white); }

  .brand-mark {
    position: absolute; border-radius: 50%;
    background: var(--accent-blue);
  }
  .brand-name {
    position: absolute; left: 0; width: 100%; text-align: center;
    font-family: "Montserrat", sans-serif; font-weight: 700;
    color: var(--accent-blue); letter-spacing: 0.06em; white-space: nowrap;
  }
  .brand-tagline {
    position: absolute; left: 0; width: 100%; text-align: center;
    font-family: "Montserrat", sans-serif; font-weight: 600;
    color: var(--muted-white); letter-spacing: 0.14em; white-space: nowrap;
  }

  .card--front .brand-mark { left: 286px; top: 108px; width: 82px; height: 82px; }
  .card--front .brand-name { top: 232px; font-size: 25px; }
  .card--front .brand-tagline { top: 283px; font-size: 9.5px; }

  .back-panel {
    position: absolute; left: 0; top: 0; width: 262px; height: 100%;
    background: var(--card-black);
    border-right: 4px solid var(--accent-blue);
  }
  .back-panel .brand-mark { left: 106px; top: 129px; width: 48px; height: 48px; }
  .back-panel .brand-name { top: 208px; font-size: 14.5px; }
  .back-panel .brand-tagline { top: 244px; font-size: 6px; }

  .details {
    position: absolute; left: 262px; top: 0; width: 390px; height: 100%;
    font-family: "Josefin Sans", sans-serif; color: var(--ink);
  }
  .person-name {
    position: absolute; top: 36px; left: 0; width: 100%; text-align: center;
    font-size: 25px; font-weight: 400; letter-spacing: 0.12em;
  }
  .person-title {
    position: absolute; top: 70px; left: 0; width: 100%; text-align: center;
    font-size: 16px; font-weight: 400; letter-spacing: 0.14em; color: var(--accent-blue);
  }
  .divider {
    position: absolute; left: 22px; width: 346px; height: 0;
    border: none;
    border-top: 1.5px dashed var(--accent-blue);
  }
  .divider--top { top: 111px; }
  .divider--bottom { top: 225px; }

  .contact-list { list-style: none; }
  .contact-item {
    position: absolute; left: 22px;
    display: flex; align-items: center; gap: 8px;
    font-size: 14px; letter-spacing: 0.03em; white-space: nowrap;
  }
  .contact-item svg { width: 16px; height: 16px; flex: none; }
  .contact-item--phone { top: 128px; font-size: 17px; letter-spacing: 0.12em; }
  .contact-item--email { top: 157px; }
  .contact-item--web { top: 186px; }

  .pin-icon { position: absolute; top: 242px; left: 188px; width: 14px; height: 18px; }

  .address {
    position: absolute; top: 266px; left: 0; width: 100%; text-align: center;
    font-style: normal; letter-spacing: 0.08em; line-height: 18.5px; font-size: 14.5px;
  }
  .address-venue { font-size: 19px; letter-spacing: 0.1em; display: block; margin-bottom: 2px; }
</style>
</head>
<body>
<main class="stage">

  <section class="card card--front" aria-label="Card front">
    <span class="brand-mark" aria-hidden="true"></span>
    <p class="brand-name">GOLD TIDE PICTURES</p>
    <p class="brand-tagline">A MEDIA ENTERTAINMENT COMPANY</p>
  </section>

  <section class="card card--back" aria-label="Card back">
    <div class="back-panel">
      <span class="brand-mark" aria-hidden="true"></span>
      <p class="brand-name">GOLD TIDE PICTURES</p>
      <p class="brand-tagline">A MEDIA ENTERTAINMENT COMPANY</p>
    </div>

    <div class="details">
      <h1 class="person-name">NEIL PARKER</h1>
      <p class="person-title">MANAGING PARTNER</p>
      <hr class="divider divider--top">

      <ul class="contact-list">
        <li class="contact-item contact-item--phone">
          <svg viewBox="0 0 16 16" aria-hidden="true"><path fill="#1ba7e2" d="M3.2 1.2l2.4 2.9-1.3 1.7c.9 2.1 2.6 3.9 4.8 4.9l1.7-1.3 2.9 2.4-1.4 2.6C6.6 14.1 1.6 9.2 1 3z"/></svg>
          (310) 555 0148
        </li>
        <li class="contact-item contact-item--email">
          <svg viewBox="0 0 16 16" aria-hidden="true"><rect x="1.5" y="3.5" width="13" height="9" fill="none" stroke="#1ba7e2" stroke-width="1.4"/><path d="M1.5 3.5L8 9l6.5-5.5" fill="none" stroke="#1ba7e2" stroke-width="1.4"/></svg>
          NEIL@GOLDTIDEPICTURESGROUP.EXAMPLE
        </li>
        <li class="contact-item contact-item--web">
          <svg viewBox="0 0 16 16" aria-hidden="true"><circle cx="6.5" cy="6.5" r="4.5" fill="none" stroke="#1ba7e2" stroke-width="1.8"/><path d="M10 10l4.5 4.5" stroke="#1ba7e2" stroke-width="2" stroke-linecap="round"/></svg>
          GOLDTIDEPICTURESGROUP.EXAMPLE
        </li>
      </ul>

      <hr class="divider divider--bottom">

      <svg class="pin-icon" viewBox="0 0 14 18" aria-hidden="true"><path fill="#1ba7e2" d="M7 0C3.4 0 1 2.6 1 6c0 4 6 12 6 12s6-8 6-12c0-3.4-2.4-6-6-6zm0 8.3A2.3 2.3 0 1 1 7 3.7a2.3 2.3 0 0 1 0 4.6z"/></svg>

      <address class="address">
        <span class="address-venue">KTW STUDIO PARK</span>
        2250 HALVERD STREET<br>
        HARBOR WING, 4TH FLOOR<br>
        MANHATTAN BEACH, CA 90412
      </address>
    </div>
  </section>

</main>
</body>
</html>
```